Patent Law

Need to develop a home page for a patent lawyer.

Colors should go with logo, blues...

Company Name- Velun Tresk, PLLC

Company Overview-

I am an Intellectual Property Lawyer and focus on patents, copyrights, trademarks, & trade secrets. I work with small businesses and start ups in the chemical and biotech industries.

Why Us-

I am small firm that can provide large-firm service at a reasonable price. I also can charge flat-fees for entreprenuers in certain practice areas.

Services-
Intellectual Property
Patents
Copyrights
Trademarks
Trade secrets
Healthcare Compliance
Elder law
Wills
Trusts

Website we like-
http://www.quorvantlegal.example/ - within industry!!
http://www.daltrowemiko.example/
http://ulbrixtane.example/
http://thegravelcounsel.example/

Target Market(s)

My customers will be small business, specifically small start-up companies in the chemical and biotech arena.

Industry/Entity Type

Trade

Requirements
Must have
• Colors should go with logo, blues...

```html
<!DOCTYPE html>
<html lang="en">
<head>
<meta charset="utf-8">
<title>Velun Tresk, PLLC — Legal Help</title>
<link rel="stylesheet" href="https://fonts.googleapis.com/css2?family=Open+Sans:wght@400;600;700&display=swap">
<style>
:root{
  --blue:#1a9fe0;
  --blue-dark:#0d83c2;
  --ink:#222;
  --text:#555;
  --dark:#1b1b1b;
  --band:#161616;
  --page:#efefef;
  --header:#edf0f4;
  --white:#fff;
}
*{box-sizing:border-box;margin:0;padding:0}
html,body{width:1086px;height:1200px;overflow:hidden}
body{font-family:"Open Sans",Arial,sans-serif;background:var(--page);position:relative;color:var(--text)}
.abs{position:absolute}

/* header */
.site-header{left:0;top:0;width:1086px;height:86px;background:var(--header)}
.brand{left:217px;top:52px;display:flex;align-items:center;gap:7px}
.brand-mark{width:14px;height:14px;border-radius:50%;background:var(--blue)}
.brand-name{font-size:11.5px;color:#2a3a5a;letter-spacing:.6px;font-weight:400;white-space:nowrap}
.social{left:614px;top:34px;display:flex;gap:4px}
.social span{width:16px;height:16px;border-radius:50%;display:block}
.btn{background:var(--blue);color:var(--white);font-weight:700;border-radius:3px;border-bottom:2px solid var(--blue-dark);display:flex;align-items:center;justify-content:center;white-space:nowrap}
.phone{left:741px;top:30px;width:83px;height:23px;font-size:10.5px}
.map{left:829px;top:30px;width:35px;height:23px;font-size:10.5px}

/* nav */
.main-nav{left:0;top:86px;width:1086px;height:35px;background:var(--blue)}
.main-nav a{position:absolute;top:0;height:35px;line-height:35px;color:var(--white);font-size:9.5px;font-weight:600;text-decoration:none}
.nav-sep{position:absolute;top:0;width:1px;height:35px;background:#1488c3}

/* hero */
.hero{left:0;top:121px;width:1086px;height:336px;background:radial-gradient(ellipse at 45% 40%,#6e7680 0%,#3c434c 45%,#1f242a 100%)}
.hero-art{left:559px;top:0;width:305px;height:330px;background:radial-gradient(ellipse at 55% 55%,#d9b766 0%,#9b7a35 38%,rgba(60,50,30,0) 72%)}
.hero h1{left:217px;top:82px;width:400px;font-size:37px;line-height:43px;font-weight:700;color:var(--white)}
.hero p{left:217px;top:173px;width:330px;font-size:11.2px;line-height:16px;font-weight:700;color:var(--white)}
.hero .read{left:217px;top:232px;width:83px;height:31px;font-size:10.5px}

/* offer band */
.offer{left:0;top:457px;width:1086px;height:65px;background:var(--band);border-bottom:2px dashed #3a3a3a}
.offer p{left:217px;top:17px;font-size:20px;color:var(--white);white-space:nowrap}
.offer .free{left:780px;top:18px;width:83px;height:31px;font-size:12px}

/* feature cards */
.card{top:545px;width:205px;height:152px;background:#2a2a2a;overflow:hidden}
.card-media{width:100%;height:125px}
.card-caption{position:absolute;left:0;bottom:0;width:100%;height:27px;background:#000;color:var(--blue);font-size:12px;text-align:center;line-height:27px}
.why h3{position:absolute;top:35px;width:100%;text-align:center;color:var(--blue);font-size:12px;font-weight:400}
.why p{position:absolute;top:58px;left:20px;width:165px;text-align:center;color:var(--white);font-family:Arial,sans-serif;font-size:8.5px;line-height:13px}

/* news and testimonial */
.section-title{font-size:15px;color:var(--ink);font-weight:400;top:731px;white-space:nowrap}
.news-photo{left:217px;top:757px;width:151px;height:113px;background:linear-gradient(135deg,#d8cfc4,#6a5a4e 60%,#1d1d1d)}
.news-title{left:375px;top:753px;font-size:9px;font-weight:600;color:var(--blue);white-space:nowrap}
.news-meta{left:375px;top:768px;font-size:8px}
.news-body{left:375px;top:786px;width:207px;font-size:8.5px;line-height:12.2px;text-align:justify}
.news-more{left:375px;top:845px;width:64px;height:24px;font-size:9.5px;font-weight:400}
.dots{left:549px;top:756px;display:flex;gap:3px}
.dots span{width:9px;height:9px;border-radius:50%;background:#bbb}
.quote-photo{left:601px;top:760px;width:94px;height:94px;border-radius:50%;background:radial-gradient(circle,#e1b79a,#a87256 70%,#e8e8e8)}
.quote{left:707px;top:760px;width:159px;font-size:8.5px;line-height:12.2px;text-align:justify}
.quote-name{left:707px;top:838px;font-size:9px;color:var(--blue)}
.quote-role{left:707px;top:851px;font-size:9px}

/* partners */
.partners{left:0;top:896px;width:1086px;height:65px;background:var(--white)}
.partner{position:absolute;top:23px;display:flex;align-items:center;gap:5px;font-size:14px;font-weight:600;color:#888;white-space:nowrap}
.partner i{width:13px;height:13px;border-radius:50%;background:#aaa;display:block}

/* footer */
.site-footer{left:0;top:961px;width:1086px;height:202px;background:var(--dark);color:#eee;font-size:8.3px;line-height:11.6px}
.tab{position:absolute;top:22px;height:20px;padding:0 6px;background:var(--blue);color:var(--white);font-weight:600;font-size:10px;line-height:20px;white-space:nowrap}
.foot-about{left:217px;top:61px;width:210px}
.foot-about p+p{margin-top:11.6px}
.links{left:478px;top:61px;list-style:none}
.links li{height:17px;padding-left:6px;position:relative}
.links li::before{content:"";position:absolute;left:0;top:3px;border-left:3px solid #eee;border-top:3px solid transparent;border-bottom:3px solid transparent}
.post-thumb{left:601px;width:55px;height:52px;background:linear-gradient(160deg,#c9b8a8,#5b5550)}
.post-text{left:664px;width:205px}
.post-date{color:var(--blue);display:block;margin-top:3px}

/* bottom bar */
.bottom-bar{left:0;top:1163px;width:1086px;height:37px;background:var(--white);font-size:8.8px;color:#444}
.bottom-bar .copy{left:217px;top:13px;white-space:nowrap}
.bottom-bar .copy span{color:var(--blue)}
.bottom-bar .foot-nav{right:224px;top:13px;white-space:nowrap}
</style>
</head>
<body>

<header class="site-header abs">
  <div class="brand abs"><span class="brand-mark"></span><span class="brand-name">VELUN TRESK, PLLC</span></div>
  <div class="social abs">
    <span style="background:#d94c4c"></span><span style="background:#3b5d9c"></span><span style="background:#3db4e6"></span><span style="background:#1d79b0"></span><span style="background:#d8433a"></span><span style="background:#d4473c"></span>
  </div>
  <div class="btn phone abs">555 014 2286</div>
  <div class="btn map abs">MAP</div>
</header>

<nav class="main-nav abs">
  <a style="left:217px">HOME</a><span class="nav-sep" style="left:265px"></span>
  <a style="left:286px">ABOUT US</a><span class="nav-sep" style="left:352px"></span>
  <a style="left:374px">PRACTICE AREA</a><span class="nav-sep" style="left:461px"></span>
  <a style="left:483px">LAWYERS</a><span class="nav-sep" style="left:545px"></span>
  <a style="left:566px">CONTACT US</a>
</nav>

<section class="hero abs">
  <div class="hero-art abs" role="img" aria-label="Golden scales of justice"></div>
  <h1 class="abs">WE PROVIDE LEGAL HELP FOR YOU!</h1>
  <p class="abs">The point of using Lorem Ipsum is that it has a more-or-less normal distribution of letters, as opposed to using Content here, content it look like readable English.</p>
  <div class="btn read abs">Read More</div>
</section>

<section class="offer abs">
  <p class="abs">We offer our clients an Expert &amp; General legal advice.</p>
  <div class="btn free abs">Free Advice</div>
</section>

<div class="card why abs" style="left:217px;background:linear-gradient(150deg,#3a3a3a,#111)">
  <h3>WHY US?</h3>
  <p>Lorem ipsum dolor sit amet, consectetuer adipiscing elit, sed diam nonummy nibh euismod tincidunt ut laoreet dolore magna aliquam erat volutpat enim ad minim veniam, quis nostrud exerce.</p>
</div>
<div class="card abs" style="left:437px">
  <div class="card-media" role="img" aria-label="Smiling lawyer at a laptop in an office" style="background:linear-gradient(135deg,#d7dde2,#8d969e 60%,#4a4f55)"></div>
  <div class="card-caption">WHAT WE DO</div>
</div>
<div class="card abs" style="left:657px">
  <div class="card-media" role="img" aria-label="Street map of the office area" style="background:linear-gradient(135deg,#e9e4d4,#d8d2b8 60%,#b9cfd8)"></div>
  <div class="card-caption">CONTACT INFO</div>
</div>

<h2 class="section-title abs" style="left:217px">LATEST NEWS</h2>
<div class="news-photo abs" role="img" aria-label="Smiling man in glasses and suit"></div>
<div class="news-title abs">LOREM IPSUM USE MANY WEBSITES</div>
<div class="dots abs"><span></span><span></span><span></span></div>
<div class="news-meta abs">Nov 18, 2013 | Lorum Lipsum</div>
<p class="news-body abs">Aarious version have evolve over the many years sometimes by accident, sometimes on purpose first true generator on the Internet Aarious version have evolve over the many years sometimes.</p>
<div class="btn news-more abs">Read more</div>

<h2 class="section-title abs" style="left:601px">WHAT PEOPLE SAY’S</h2>
<div class="quote-photo abs" role="img" aria-label="Portrait of a client"></div>
<p class="quote abs">Aarious version have evolve over the many years sometimes by accident, sometimes on purpose first true generator on the Internet Aarious version have evolve over the many years sometimes.</p>
<div class="quote-name abs">-Maren Holt</div>
<div class="quote-role abs">Customer</div>

<section class="partners abs">
  <div class="partner" style="left:222px"><i></i>Corvalis</div>
  <div class="partner" style="left:356px"><i></i>PELLO HOST</div>
  <div class="partner" style="left:500px">TARVO HOST</div>
  <div class="partner" style="left:637px"><i></i>Kestrel Nine</div>
  <div class="partner" style="left:788px"><i></i>ondrava</div>
</section>

<footer class="site-footer abs">
  <div class="tab" style="left:217px">About Us</div>
  <div class="tab" style="left:478px">Usefull Links</div>
  <div class="tab" style="left:601px;padding:0 10px">Latest Post</div>
  <div class="foot-about abs">
    <p>Sestibulum luctus ipsum id quam euismod a malesuada sapien euismot. Vesti bulum elementum interdum.</p>
    <p>Lorem ipsum dolor sit amet elit, consectetur adipiscing. Vestibulum luctus ipsum id quam euismod a malesuada sapien euismot. Vesti bulum elementum interdum.</p>
  </div>
  <ul class="links abs">
    <li>New resources</li><li>About our company</li><li>What we do</li><li>Latest Updates</li><li>Our blog</li><li>Newsletter</li>
  </ul>
  <div class="post-thumb abs" style="top:58px" role="img" aria-label="Portrait of a lawyer"></div>
  <p class="post-text abs" style="top:57px">Lorem ipsum dolor sit amet elit, and the lorum lipsum consectetur adipiscing. Vestibulum luctus ipsum id quam euismod a malesuada sapien.<span class="post-date">13 January 2014</span></p>
  <div class="post-thumb abs" style="top:129px" role="img" aria-label="Portrait of a lawyer"></div>
  <p class="post-text abs" style="top:128px">Lorem ipsum dolor sit amet elit, and the lorum lipsum consectetur adipiscing. Vestibulum luctus ipsum id quam euismod a malesuada sapien.<span class="post-date">13 January 2014</span></p>
</footer>

<div class="bottom-bar abs">
  <p class="copy abs">Copyrights 2014.<span>VELUN TRESK,PLLC</span>, All Rights Reserved.</p>
  <p class="foot-nav abs">Home &nbsp;|&nbsp; About Us &nbsp;|&nbsp; Practice Area &nbsp;|&nbsp; Lawyers &nbsp;|&nbsp; Contact Us</p>
</div>

</body>
</html>
```